ORLA - Óptica Médica - web design and concept

Website concept - Create and develop our website design and structure. ORLA is an optical store chain, and we are looking to establish our web and digital concept. In attachment there are several pictures about our stores and our logo.

The website structure should be user friendly. Colors should be light and the design as simple and minimalist as possible. There are different variations of the logothat can be used, check the file.

The website will include optical collections and sun collections as an online store. Also, a medical menu should be considered in order for clients to schedule optometry appointments. There should also be a menu for client assistance where the clients can read about glass maintenance in our workshop.
Updates

Low design quality

Number of Pages Required

5+ page

Font styles to use
Serif
Sans Serif

Requirements
Must have
• Must be user-friendly and minimalist.
• Please USE PICTURES FROM THE BRANDS we sell: MERUN, BOSKA, PNW, KOLE, BAMPE
Nice to have
• Nice to inspire: ZEK glasses (see website https://ch.shopzek.com/en/)
• Nice to inspire: https://merun-eyewear.com/
• Nice to ispire: https://www.pnwglobe.com/en/
Should not have
• Hysteric colors and shapes

```html
<!DOCTYPE html>
<html lang="en">
<head>
<meta charset="utf-8">
<title>ORLA – Product</title>
<link href="https://fonts.googleapis.com/css2?family=Poppins:wght@300;400;500;600&display=swap" rel="stylesheet">
<style>
:root{
  --accent:#efb24b;
  --ink:#222;
  --muted:#777;
  --line:#e2e2e2;
  --band:#efefef;
  --footer:#0c0c0c;
  --white:#fff;
}
*{box-sizing:border-box;margin:0;padding:0}
html,body{width:1200px;height:2284px;overflow:hidden;background:var(--white)}
body{font-family:"Poppins",sans-serif;color:var(--ink);position:relative}
.abs{position:absolute}
/* header */
.topbar{top:0;left:0;width:1200px;height:88px}
.social{left:160px;top:14px;display:flex;gap:10px}
.social span{width:12px;height:12px;border-radius:50%;background:#333;display:block}
.brand{left:0;width:1200px;top:16px;text-align:center}
.brand b{font-weight:600;font-size:30px;letter-spacing:6px;color:#111}
.brand i{display:block;width:10px;height:10px;background:var(--accent);margin:0 auto 4px}
.contact-top{right:160px;top:12px;font-size:11px;color:#444;display:flex;gap:18px;align-items:center}
.contact-top svg{vertical-align:-2px;margin-right:4px}
.nav{top:100px;left:0;width:1200px;display:flex;justify-content:center;align-items:center;gap:30px;font-size:13px;color:#333}
.nav .active{color:var(--accent)}
.btn{background:var(--accent);color:#fff;font-size:12px;padding:7px 18px;font-weight:500}
/* product */
.crumb{top:164px;left:160px;font-size:12px;color:#666}
.crumb em{font-style:normal;color:var(--accent)}
.hero-img{top:200px;left:160px;width:420px;height:400px;background:radial-gradient(ellipse at center,#5a5a62 0 18%,#f6f6f6 19%,#f6f6f6 100%)}
.info{top:212px;left:620px;width:420px}
.info h1{font-size:28px;font-weight:400}
.info .code{font-size:11px;color:var(--muted);margin-top:4px}
.info .price{font-size:26px;font-weight:500;margin-top:42px}
.info .price small{font-size:18px;font-weight:400}
.opts{display:flex;gap:70px;margin-top:32px;font-size:12px}
.sel{margin-top:6px;display:flex}
.sel span{border:1px solid var(--line);font-size:11px;padding:5px 12px;color:#444}
.sel b{width:26px;background:var(--accent);display:block}
.qty{margin-top:26px;font-size:12px}
.qty .sel span{padding:5px 18px}
.cart{display:inline-block;margin-top:50px;background:var(--accent);color:#fff;font-size:12px;padding:16px 42px}
.thumbs{top:668px;left:160px;width:450px;display:flex;align-items:center;justify-content:space-between}
.thumbs .g{width:58px;height:28px;background:radial-gradient(ellipse,#555 0 30%,#fff 32%)}
.arrow{font-size:26px;color:#555;line-height:1}
.arrow.y{color:var(--accent)}
.tabs{top:760px;left:160px;display:flex}
.tabs div{width:200px;height:42px;line-height:42px;text-align:center;font-size:14px}
.tabs .t1{background:var(--band)}
.tabs .t2{background:var(--accent);color:#fff;clip-path:polygon(12% 0,100% 0,100% 100%,0 100%)}
.spec{top:802px;left:0;width:1200px;height:218px;background:var(--band);padding:36px 160px;font-size:13px;line-height:30px;color:#333}
/* related */
.title{left:0;width:1200px;text-align:center;font-size:22px;font-weight:400}
.title::after{content:"";display:block;width:56px;height:2px;background:var(--accent);margin:8px auto 0}
.related{top:1136px;left:70px;width:1060px;display:flex;align-items:center;justify-content:space-between}
.prod{width:160px;text-align:center;font-size:14px}
.prod div{height:80px;margin-bottom:32px}
.p1{background:radial-gradient(ellipse,#6d7d5e 0 28%,#fff 30%)}
.p2{background:radial-gradient(ellipse,#9a5d3b 0 28%,#fff 30%)}
.p3{background:radial-gradient(ellipse,#44474f 0 28%,#fff 30%)}
.p4{background:radial-gradient(ellipse,#1e1e1e 0 28%,#fff 30%)}
.arrow.big{font-size:44px;color:#333}
/* newsletter */
.news{top:1452px;left:304px;width:596px;height:64px;border:1px solid #cfcfcf;box-shadow:0 2px 6px rgba(0,0,0,.12);display:flex}
.news span{flex:1;font-size:12px;color:#888;padding:22px 20px;border-bottom:2px solid var(--accent)}
.news b{width:100px;background:var(--accent);display:flex;align-items:center;justify-content:center}
/* brands */
.brands{top:1604px;left:70px;width:1060px;display:flex;align-items:center;justify-content:space-between}
.brands .logo{width:150px;height:116px;background:#f1f1f1;display:flex;align-items:center;justify-content:center;font-size:18px;font-weight:500;color:#111}
.brand-row{display:flex;gap:28px}
/* features */
.features{top:1798px;left:168px;display:flex;gap:16px}
.feat{width:280px;height:90px;border:1px solid var(--line);display:flex;align-items:center;gap:14px;padding:0 22px}
.feat i{width:40px;height:40px;border:2px solid var(--accent);border-radius:50%;flex:none}
.feat b{font-weight:500;font-size:13px;display:block}
.feat small{font-size:10px;color:var(--muted)}
/* footer */
.footer{top:1944px;left:0;width:1200px;height:340px;background:var(--footer);color:#ddd}
.fcol{position:absolute;top:62px;font-size:11px;line-height:20px}
.fcol h4{color:var(--accent);font-weight:500;font-size:12px;margin-bottom:10px}
.fcol li{list-style:none}
.fcol li::before{content:"›  ";color:var(--accent)}
.flogo b{font-size:24px;font-weight:600;letter-spacing:5px;color:#fff;display:block;margin-bottom:10px}
.fdots{display:flex;gap:8px;margin-top:10px}
.fdots span{width:10px;height:10px;border-radius:50%;background:var(--accent)}
.fbottom{position:absolute;left:160px;right:160px;top:248px;border-top:1px solid #333;padding-top:14px;display:flex;justify-content:space-between;font-size:11px}
</style>
</head>
<body>

<header>
  <div class="abs social"><span></span><span></span><span></span><span></span></div>
  <div class="abs brand"><i></i><b>ORLA</b></div>
  <div class="abs contact-top">
    <span><svg width="11" height="11" viewBox="0 0 24 24"><path d="M6 2l4 4-2 3c1 3 4 6 7 7l3-2 4 4-3 4C10 21 3 14 2 5z" fill="#444"/></svg>+351 210 440 000</span>
    <span><svg width="12" height="10" viewBox="0 0 24 18"><rect x="1" y="1" width="22" height="16" fill="none" stroke="#444" stroke-width="2"/><path d="M1 1l11 9 11-9" fill="none" stroke="#444" stroke-width="2"/></svg>hello@orla-optica.pt</span>
  </div>
  <nav class="abs nav">
    <span>Home</span><span class="active">Sun</span><span>Optical</span><span>Kids</span><span>Contact Us</span>
    <span class="btn">Book an Appointment</span>
  </nav>
</header>

<main>
  <div class="abs crumb">Home / Sun / <em>Product Name</em></div>
  <div class="abs hero-img" role="img" aria-label="Product photo: black sunglasses with dark lenses"></div>

  <section class="abs info">
    <h1>Product Name</h1>
    <p class="code">Code: 18845</p>
    <p class="price">30.00 <small>EUR</small></p>
    <div class="opts">
      <div>Colour<div class="sel"><span>Black</span><b></b></div></div>
      <div>Size<div class="sel"><span>Medium</span><b></b></div></div>
    </div>
    <div class="qty">QTY<div class="sel"><span>1</span><b></b></div></div>
    <span class="cart">ADD TO CART</span>
  </section>

  <div class="abs thumbs">
    <span class="arrow">‹</span>
    <div class="g" role="img" aria-label="Sunglasses view"></div>
    <div class="g" role="img" aria-label="Sunglasses view"></div>
    <div class="g" role="img" aria-label="Sunglasses view"></div>
    <div class="g" role="img" aria-label="Sunglasses view"></div>
    <div class="g" role="img" aria-label="Sunglasses view"></div>
    <span class="arrow y">›</span>
  </div>

  <div class="abs tabs"><div class="t1">Description</div><div class="t2">Loream</div></div>
  <div class="abs spec">
    SIZE: MEDIUM<br>MEASUREMENTS - 53x22x145<br>SWISS DESIGN<br>HANDMADE IN
  </div>

  <h2 class="abs title" style="top:1068px">Related Product</h2>
  <div class="abs related">
    <span class="arrow big">‹</span>
    <div class="prod"><div class="p1" role="img" aria-label="Green aviator sunglasses"></div>Product Name</div>
    <div class="prod"><div class="p2" role="img" aria-label="Tortoise optical frames"></div>Product Name</div>
    <div class="prod"><div class="p3" role="img" aria-label="Dark round sunglasses"></div>Product Name</div>
    <div class="prod"><div class="p4" role="img" aria-label="Black sunglasses"></div>Product Name</div>
    <span class="arrow big">›</span>
  </div>

  <h2 class="abs title" style="top:1378px">Subscribe For Our Newsletter</h2>
  <div class="abs news">
    <span>E-Mail Address</span>
    <b><svg width="30" height="24" viewBox="0 0 30 24"><path d="M2 2l26 10L2 22l4-10z" fill="#fff"/></svg></b>
  </div>

  <div class="abs brands">
    <span class="arrow big">‹</span>
    <div class="brand-row">
      <div class="logo">Solvane</div>
      <div class="logo">Halcor</div>
      <div class="logo">Mirelle</div>
      <div class="logo">Sereth</div>
      <div class="logo">Ovan</div>
    </div>
    <span class="arrow big y">›</span>
  </div>

  <div class="abs features">
    <div class="feat"><i></i><div><b>Free Shipping</b><small>Local orders in two days</small></div></div>
    <div class="feat"><i></i><div><b>Premium Support</b><small>24/7 customer service</small></div></div>
    <div class="feat"><i></i><div><b>Payment Method</b><small>Card and bank transfer</small></div></div>
  </div>
</main>

<footer class="abs footer">
  <div class="fcol flogo" style="left:160px;width:200px">
    <b>ORLA</b>
    Lorem ipsum dolor sit amet, consectetur adipiscing elit, sed do eiusmod tempor.
    <div class="fdots"><span></span><span></span><span></span><span></span></div>
  </div>
  <div class="fcol" style="left:420px"><h4>QUICK LINK</h4><ul><li>Home</li><li>Sun</li><li>Optical</li><li>Collections</li><li>Contact Us</li></ul></div>
  <div class="fcol" style="left:640px"><h4>ACCOUNT</h4><ul><li>My Account</li><li>My Wishlist</li><li>Checkout</li><li>Create Account</li><li>Register</li></ul></div>
  <div class="fcol" style="left:860px;width:200px"><h4>QUICK CONTACT</h4>
    +351 210 440 000<br>hello@orla-optica.pt<br>Rua das Flores 18,<br>1200-195 Lisboa, Portugal
  </div>
  <div class="fbottom"><span>Copyright - © 2018 ORLA Óptica Médica. All Rights Reserved</span><span>Privacy Policy - Terms &amp; Conditions</span></div>
</footer>

</body>
</html>
```